Business Card and Letterhead for Pimlu - modern real estate business

I need a double sided business card design for Pimlu. Please see business card brief here https://files.trelvonadocs.com/sheet/r/7QzTmWbaXLJnoPEd-kRyUgFhHsstbvCe2qfoMxDa_pz/view?mode=shared

Please feel free to design the business cards however you feel best. I am happy to give some creative freedoms and then provide feedback from there.

Please then also create a letterhead to match the business card design

Colors

Designer to choose colors to be used in the design.

Requirements
Must have
• Must be a modern, elegant business card which looks very professional

```html
<!DOCTYPE html>
<html lang="en">
<head>
<meta charset="utf-8">
<title>Pimlu Business Card</title>
<link href="https://fonts.googleapis.com/css2?family=Michroma&family=Open+Sans:wght@300;400&display=swap" rel="stylesheet">
<style>
  :root {
    --backdrop: #333333;
    --card-light: #f4f2f3;
    --card-dark: #0d0d0d;
    --brand-red: #e21f26;
    --brand-red-deep: #cc0a0f;
    --ink: #231f20;
    --white: #ffffff;
    --photo-top: #9fb3b8;
    --photo-bottom: #2a2b2e;
  }
  * { margin: 0; padding: 0; box-sizing: border-box; }
  html, body {
    width: 903px;
    height: 1200px;
    overflow: hidden;
    background: var(--backdrop);
  }
  .canvas {
    position: relative;
    width: 903px;
    height: 1200px;
  }
  .card {
    position: absolute;
    width: 548px;
    height: 339px;
    overflow: hidden;
  }
  .card--front { left: 173px; top: 191px; background: var(--card-light); }
  .card--back  { left: 184px; top: 631px; background: var(--card-dark); }

  .wordmark {
    font-family: "Michroma", sans-serif;
    color: var(--brand-red);
    line-height: 1;
    letter-spacing: 1px;
  }
  .card--front .wordmark {
    position: absolute;
    left: 42px;
    top: 42px;
    font-size: 36px;
  }
  .card--back .wordmark {
    position: absolute;
    left: 0;
    right: 0;
    top: 132px;
    text-align: center;
    font-size: 64px;
    color: var(--brand-red-deep);
  }

  .agent-photo {
    position: absolute;
    left: 429px;
    top: -3px;
    width: 122px;
    height: 194px;
    border-left: 3px solid var(--brand-red);
    border-bottom: 3px solid var(--brand-red);
    border-bottom-left-radius: 14px;
    background: linear-gradient(180deg, var(--photo-top) 0%, #5d6a5a 35%, var(--photo-bottom) 70%);
  }

  .contact {
    position: absolute;
    font-family: "Open Sans", sans-serif;
    font-weight: 300;
    font-size: 12px;
    line-height: 15.7px;
    color: var(--ink);
  }
  .contact--office { left: 42px; top: 213px; }
  .contact--agent { right: 45px; top: 213px; text-align: right; }
  .agent-name {
    font-family: "Michroma", sans-serif;
    font-weight: 400;
    font-size: 15px;
    line-height: 22px;
    letter-spacing: 0.5px;
    color: var(--ink);
  }

  .web-band {
    position: absolute;
    left: 0;
    right: 0;
    bottom: 0;
    height: 25px;
    background: var(--brand-red);
    color: var(--white);
    font-family: "Open Sans", sans-serif;
    font-weight: 400;
    font-size: 13px;
    line-height: 25px;
    text-align: center;
  }
</style>
</head>
<body>
<main class="canvas">
  <section class="card card--front" aria-label="Business card front">
    <div class="wordmark">PIMLU</div>
    <div class="agent-photo" role="img" aria-label="Portrait photo of the agent outdoors"></div>
    <div class="contact contact--office">
      <p>Lic No. 10384215</p>
      <p>PO Box 5310</p>
      <p>Hillcrest NSW 2790</p>
      <p>02 4810 3597</p>
      <p>info@pimlu.com</p>
    </div>
    <div class="contact contact--agent">
      <p class="agent-name">MARCUS HALE</p>
      <p>Licenced Real Estate Agent</p>
      <p>Lic No. 20471936</p>
      <p>0431 608 274</p>
      <p>marcus@pimlu.com</p>
    </div>
    <div class="web-band">www.pimlu.com</div>
  </section>

  <section class="card card--back" aria-label="Business card back">
    <div class="wordmark">PIMLU</div>
  </section>
</main>
</body>
</html>
```